Staff Newsletter Template Image

We are looking for two .jpg images that we can put into a Word document and use for our staff newsletter. We will then add content using text boxes.
Attached is the current template which works for the columns and size that we need but we just want a fresh new design.
The Word document shows how we use it.
The name will stay the same - Brightwave Post but can be a different look to the current one.

Target Market(s)

Sales team

Colors

Designer to choose colors to be used in the design.

Requirements
Must have
• Colours will be green, grey and white, possibly cream if needed. All from the guidelines.
• I have attached our brand guidelines which shows design elements and fonts for our brand. Also attached is brand guidelines for one of our product lines as we would like to use the same green.
• It needs to be nice to look at and motivational for our team

```html
<!DOCTYPE html>
<html lang="en">
<head>
<meta charset="utf-8">
<title>Brightwave Post – Staff Newsletter</title>
<link rel="stylesheet" href="https://fonts.googleapis.com/css2?family=Cinzel:wght@500&display=swap">
<style>
  :root {
    --paper: #ffffff;
    --green: #8cc63f;
    --green-light: #a5cf50;
    --charcoal: #2a2b36;
    --slate: #45474d;
    --ink-light: #ffffff;
  }
  html, body {
    margin: 0;
    padding: 0;
    overflow: hidden;
    background: var(--paper);
  }
  .newsletter-page {
    position: relative;
    width: 884px;
    height: 1200px;
    background: var(--paper);
    overflow: hidden;
  }
  .header-waves,
  .footer-waves {
    position: absolute;
    left: 0;
    width: 884px;
    display: block;
  }
  .header-waves { top: 0; height: 260px; }
  .footer-waves { bottom: 0; height: 260px; }
  .masthead-name {
    position: absolute;
    top: 72px;
    left: 28px;
    width: 150px;
    margin: 0;
    font-family: "Cinzel", serif;
    font-weight: 500;
    font-size: 19px;
    line-height: 1.15;
    letter-spacing: 0.5px;
    color: var(--ink-light);
    text-align: center;
  }
</style>
</head>
<body>
  <main class="newsletter-page">
    <svg class="header-waves" viewBox="0 0 884 260" aria-hidden="true">
      <path fill="var(--charcoal)" d="M300 150 C500 80 760 95 884 238 L884 60 L300 60 Z"/>
      <path fill="var(--slate)" d="M320 145 C520 85 740 92 860 205 C760 120 540 110 330 150 Z"/>
      <path fill="var(--green)" d="M0 0 H884 V85 C700 70 450 108 300 148 C200 172 100 188 0 190 Z"/>
      <path fill="var(--green-light)" d="M0 0 H430 C415 95 330 155 220 172 C150 182 70 188 0 190 Z"/>
    </svg>

    <p class="masthead-name">Brightwave Post</p>

    <svg class="footer-waves" viewBox="0 0 884 260" aria-hidden="true">
      <path fill="var(--charcoal)" d="M0 60 C50 140 250 172 500 168 L884 150 V260 H0 Z"/>
      <path fill="var(--slate)" d="M0 40 C40 120 200 160 420 166 C250 175 60 150 0 110 Z"/>
      <path fill="var(--green)" d="M0 192 C300 200 520 150 884 112 V260 H0 Z"/>
    </svg>
  </main>
</body>
</html>
```